Business card design needed

Family General Practitioner/ Family Physician.
Logo is the logo of the Noble Guild of Family Healers Oceania
http://kpltw.varendo.example/ImageShelf/marks/pages/NGFHO%20mark_jpg.htm
Updates

Project Deadline Extended
Reason: Just a bit more time to make changes and the weekend for me to look at things closely and to choose. Thanks, Orin

Thanks for all the submissions. So many of them are really works of art. Not one of them are not good. The ones that I am eliminating are the ones that I think are not suitable for me personally only, and because if I don't, it makes it very difficult to decide as many of you are also sending me slight variations of a card. I have just decided to choose a second place card too. Can't thank you all enough. Good luck, Orin. P.S - Working today till 10 pm as the card says :-), so probably won't be able to give a feedback till late Saturday night or Sunday morning here in Sydney, Australia. 

Project Deadline Extended
Reason: Just added a second place to the budget and realised that Australia is ahead of the rest of the world in the time zone (only :-) - don't want to offend anyone or start a debate!! ) , so Monday deadline will mean it will be a weekend for the rest of the world. Just wanted to give everyone more time to submit their best, especially since I will be picking a second card too. Can't thank everyone enough for the submissions. P.S - Not keen on photos on the card.

Industry/Entity Type

Business

Contact Information for Business Card

Dr. Orin Halvey M.B.B.S., F.N.G.F.H.O
Family General Practitioner
Address, timings, phone and fax number on the back.

Requirements
Must have
• Timings
Mon 7 am - 7 pm
Tues 7 am - 12 pm
Wed 7 am - 10 pm
Thurs 7 am - 12 pm
Fri 7 am - 8 pm
Sat 8 am - 10 pm
Sun - Off

```html
<!DOCTYPE html>
<html lang="en">
<head>
<meta charset="utf-8">
<title>Dr. Orin Halvey – Business Card Options</title>
<link rel="stylesheet" href="https://fonts.googleapis.com/css2?family=Cinzel:wght@400;600&family=Open+Sans:wght@400;700&family=Tinos:wght@400;700&display=swap">
<style>
  :root {
    --page: #e9e4dc;
    --navy-deep: #233a55;
    --navy-mid: #2b5784;
    --navy-glow: #2f6399;
    --crimson: #9e1c22;
    --crimson-dark: #6e1a1a;
    --brown: #4a2416;
    --gold: #c9a75a;
    --green: #7da34a;
    --rule: #8b97a6;
    --white: #ffffff;
    --label: #ffffff;
    --label-shadow: rgba(0,0,0,.35);
  }
  * { box-sizing: border-box; margin: 0; padding: 0; }
  html, body { width: 1200px; height: 809px; overflow: hidden; }
  body { background: var(--page); position: relative; font-family: "Open Sans", Arial, sans-serif; }

  .card {
    position: absolute; width: 537px; height: 308px; overflow: hidden;
    box-shadow: 0 2px 6px rgba(0,0,0,.25);
    background: radial-gradient(ellipse at 60% 30%, var(--navy-glow) 0%, var(--navy-mid) 35%, var(--navy-deep) 100%);
  }
  .card--front { left: 43px; top: 53px; }
  .card--back-1 { left: 605px; top: 56px; }
  .card--back-2 { left: 39px; top: 420px; }
  .card--back-3 { left: 608px; top: 425px; }

  /* Front */
  .front-art { position: absolute; inset: 0; }
  .doctor-name {
    position: absolute; top: 30px; left: 0; width: 100%; text-align: center;
    font-family: "Cinzel", "Times New Roman", serif; font-size: 40px; letter-spacing: 2px;
    color: var(--white); font-weight: 400;
  }
  .doctor-credentials {
    position: absolute; top: 84px; left: 0; width: 100%; text-align: center;
    font-family: "Tinos", "Times New Roman", serif; font-size: 12px; letter-spacing: 1px; color: #dfe6ee;
  }
  .doctor-role {
    position: absolute; top: 122px; left: 0; width: 100%; text-align: center;
    font-family: "Tinos", "Times New Roman", serif; font-size: 19px; letter-spacing: 2px; color: var(--white);
  }
  .tagline {
    position: absolute; bottom: 10px; left: 115px;
    font-family: "Tinos", "Times New Roman", serif; font-weight: 700; font-size: 23px; color: var(--white);
  }
  .guild-mark {
    position: absolute; right: 22px; bottom: 14px; width: 96px;
    font-family: "Tinos", "Times New Roman", serif; font-size: 11px; line-height: 1.25;
    color: var(--white); text-align: center;
  }
  .guild-mark--faint {
    right: 40px; top: 40px; bottom: auto; width: 170px; font-size: 22px; line-height: 1.2;
    color: rgba(255,255,255,.08);
  }

  /* Back */
  .hours { position: absolute; color: var(--white); }
  .hours__title { font-size: 20px; font-weight: 400; margin-bottom: 4px; }
  .hours__row { font-size: 15.5px; line-height: 23.2px; white-space: nowrap; }
  .hours__time, .hours__off { font-weight: 700; }

  .card--back-1 .hours { left: 38px; top: 16px; }
  .card--back-1 .hours__row { font-weight: 700; text-transform: uppercase; }

  .card--back-2 .hours { left: 31px; top: 6px; }
  .card--back-2 .hours__title { margin-left: 21px; letter-spacing: 1px; }
  .card--back-2 .hours__row { display: flex; }
  .card--back-2 .hours__day { width: 112px; }

  .card--back-3 .hours { left: 38px; top: 16px; }

  .contact-band {
    position: absolute; left: 0; right: 0; bottom: 0; height: 82px;
    background: var(--crimson); border-top: 2px solid var(--rule);
    font-family: "Tinos", "Times New Roman", serif; color: var(--white);
    text-align: center; font-size: 14.5px; line-height: 18px; padding-top: 10px;
  }
  .contact-band__phones { margin-top: 8px; }
  .contact-band__divider { display: inline-block; width: 1.5px; height: 18px; background: var(--white); vertical-align: -3px; margin: 0 8px; }

  .option-label {
    position: absolute; font-weight: 700; font-size: 20px; color: var(--label);
    text-shadow: 0 1px 2px var(--label-shadow);
  }
  .option-label--1 { left: 817px; top: 368px; }
  .option-label--2 { left: 252px; top: 726px; }
  .option-label--3 { left: 820px; top: 731px; }
</style>
</head>
<body>

<section class="card card--front">
  <svg class="front-art" viewBox="0 0 537 308" preserveAspectRatio="none" aria-hidden="true">
    <defs>
      <linearGradient id="band-red" x1="0" x2="1" y1="0" y2="0">
        <stop offset="0" stop-color="#4a2416"/>
        <stop offset=".45" stop-color="#7a1d1c"/>
        <stop offset="1" stop-color="#a01c22"/>
      </linearGradient>
    </defs>
    <path d="M0 262 C150 262 250 240 340 200 C420 165 480 162 537 168 L537 308 L0 308 Z" fill="url(#band-red)"/>
    <path d="M0 256 C150 255 250 232 340 192 C420 158 480 156 537 160" fill="none" stroke="#c9a75a" stroke-width="5"/>
    <path d="M0 247 C150 246 260 220 350 180 C420 152 480 148 537 150" fill="none" stroke="#7da34a" stroke-width="5"/>
    <path d="M0 252 C150 250 255 226 345 186" fill="none" stroke="#2b5784" stroke-width="2"/>
  </svg>
  <h1 class="doctor-name">Dr. Orin Halvey</h1>
  <p class="doctor-credentials">M.B.B.S., F.N.G.F.H.O</p>
  <p class="doctor-role">Family General Practitioner</p>
  <p class="tagline">Caring about your health</p>
  <p class="guild-mark">Noble Guild of Family Healers Oceania</p>
</section>

<section class="card card--back-1">
  <p class="guild-mark guild-mark--faint">Noble Guild of Family Healers Oceania</p>
  <div class="hours">
    <h2 class="hours__title">Working Hours</h2>
    <p class="hours__row">Monday&nbsp; 7 AM&nbsp; - 7 PM</p>
    <p class="hours__row">Tuesday&nbsp; 7 AM - 12 PM</p>
    <p class="hours__row">Wednesday&nbsp; 7 AM - 10 PM</p>
    <p class="hours__row">Thursday&nbsp; 7 AM - 12 PM</p>
    <p class="hours__row">Friday&nbsp;&nbsp; 7 AM&nbsp; - 8 PM</p>
    <p class="hours__row">Saturday&nbsp; 8 AM - 10 PM</p>
    <p class="hours__row">Sunday - Off</p>
  </div>
  <div class="contact-band">
    <p>Upper Level, Harbour Court, Linden Grove Shopping Centre</p>
    <p>Brookvale Hill, NSW 2199</p>
    <p class="contact-band__phones">P: 02 7300 1400<span class="contact-band__divider"></span>F: 02 7300 1455</p>
  </div>
</section>
<p class="option-label option-label--1">Option# 1</p>

<section class="card card--back-2">
  <p class="guild-mark guild-mark--faint">Noble Guild of Family Healers Oceania</p>
  <div class="hours">
    <h2 class="hours__title">Working Hours</h2>
    <p class="hours__row"><span class="hours__day">Monday</span><span class="hours__time">7 AM&nbsp; - 7 PM</span></p>
    <p class="hours__row"><span class="hours__day">Tuesday</span><span class="hours__time">7 AM - 12 PM</span></p>
    <p class="hours__row"><span class="hours__day">Wednesday</span><span class="hours__time">7 AM - 10 PM</span></p>
    <p class="hours__row"><span class="hours__day">Thursday</span><span class="hours__time">7 AM - 12 PM</span></p>
    <p class="hours__row"><span class="hours__day">Friday</span><span class="hours__time">7 AM&nbsp; - 8 PM</span></p>
    <p class="hours__row"><span class="hours__day">Saturday</span><span class="hours__time">8 AM - 10 PM</span></p>
    <p class="hours__row"><span class="hours__day">Sunday</span><span class="hours__off">OFF</span></p>
  </div>
  <div class="contact-band">
    <p>Upper Level, Harbour Court, Linden Grove Shopping Centre</p>
    <p>Brookvale Hill, NSW 2199</p>
    <p class="contact-band__phones">P: 02 7300 1400<span class="contact-band__divider"></span>F: 02 7300 1455</p>
  </div>
</section>
<p class="option-label option-label--2">Option# 2</p>

<section class="card card--back-3">
  <p class="guild-mark guild-mark--faint">Noble Guild of Family Healers Oceania</p>
  <div class="hours">
    <h2 class="hours__title">Working Hours</h2>
    <p class="hours__row">Monday&nbsp; <span class="hours__time">7 AM&nbsp; - 7 PM</span></p>
    <p class="hours__row">Tuesday&nbsp; <span class="hours__time">7 AM - 12 PM</span></p>
    <p class="hours__row">Wednesday&nbsp; <span class="hours__time">7 AM - 10 PM</span></p>
    <p class="hours__row">Thursday&nbsp; <span class="hours__time">7 AM - 12 PM</span></p>
    <p class="hours__row">Friday&nbsp;&nbsp; <span class="hours__time">7 AM&nbsp; - 8 PM</span></p>
    <p class="hours__row">Saturday&nbsp; <span class="hours__time">8 AM - 10 PM</span></p>
    <p class="hours__row">Sunday - <span class="hours__off">OFF</span></p>
  </div>
  <div class="contact-band">
    <p>Upper Level, Harbour Court, Linden Grove Shopping Centre</p>
    <p>Brookvale Hill, NSW 2199</p>
    <p class="contact-band__phones">P: 02 7300 1400<span class="contact-band__divider"></span>F: 02 7300 1455</p>
  </div>
</section>
<p class="option-label option-label--3">Option# 3</p>

</body>
</html>
```